Redo a PPT pres. - Real Estate in Brazil - Socially equitable investments in Social Housing

We need to redo the presentation attached. It is an institutional presentation to attract local and foreign investors to invest in Brazilian Social Housing Projects structured by our company "TLR".
A middle class of 100 million, a housing deficit of 9M, a strong political will & positive income generation trends constitute grounds for a significant demand in social housing.
This make a perfect scheme for investors to invest in Brazilian Social Housing.
"TLR", is a consulting "boutique" focused in Brazilian real estate, specialized in structuring, analyzing and originating Brazilian social housing projects.
TLR is part of the group TLB. TLB is structured to create value through each step of the residential real estate business - structuring, financing, sales, marketing and technology.
We would like to see designs that use mainly the color blue. The final design should communicate financial safety and professionalism. In order to reach our needs, the designer will need to have basic understanding of finance and investment in order to highlight the most important information.
The idea is to receive back the PPT with each page redesigned and an homogeneous identity.
To all designers,
Target Market(s)
Institutional Investors and wealthy individuals
Industry/Entity Type
Residential
Look and feel

```html
<!DOCTYPE html>
<html lang="en">
<head>
<meta charset="utf-8">
<title>Business Progress</title>
<link rel="stylesheet" href="https://fonts.googleapis.com/css2?family=Carlito:wght@400;700&display=swap">
<style>
  :root {
    --blue-top-a: #2f7fe0;
    --blue-top-b: #4a97ee;
    --city-a: #3b6fb8;
    --city-b: #1d3f7a;
    --navy-a: #0b2350;
    --navy-b: #1b3e7c;
    --title-blue: #1a6fb0;
    --title-dark: #111111;
    --body-text: #2b2b2b;
    --brand-blue: #45c0ee;
    --white: #ffffff;
  }
  * { margin: 0; padding: 0; box-sizing: border-box; }
  html, body { width: 1200px; height: 900px; overflow: hidden; background: var(--white); }
  body { font-family: "Carlito", "Calibri", sans-serif; position: relative; }

  .top-band {
    position: absolute; left: 0; top: 0; width: 1200px; height: 115px;
    background: linear-gradient(90deg, var(--blue-top-a) 0%, var(--blue-top-b) 50%, #5aa2ef 100%);
  }
  .top-band__skyline {
    position: absolute; right: 0; top: 0; width: 640px; height: 115px;
    background: linear-gradient(90deg, rgba(74,151,238,0) 0%, var(--city-a) 35%, var(--city-b) 100%);
  }

  .heading-fade {
    position: absolute; left: 0; top: 232px; width: 800px; height: 120px;
    background: linear-gradient(90deg, #e9e9e9 0%, #f4f4f4 45%, rgba(255,255,255,0) 100%);
    opacity: .7;
  }
  .slide-title {
    position: absolute; left: 61px; top: 180px;
    font-size: 42px; font-weight: 700; color: var(--title-dark); letter-spacing: -0.3px;
  }
  .slide-title__accent { color: var(--title-blue); }
  .slide-intro {
    position: absolute; left: 61px; top: 250px; width: 1020px;
    font-size: 21px; line-height: 36px; color: var(--body-text);
  }

  .progress-chart { position: absolute; left: 0; top: 380px; }
  .bar-label { font-family: "Carlito", "Calibri", sans-serif; font-size: 19px; fill: #111; }

  .bottom-band {
    position: absolute; left: 0; top: 758px; width: 1200px; height: 142px;
    background: linear-gradient(180deg, var(--navy-a) 0%, var(--navy-b) 100%);
  }
  .brand {
    position: absolute; left: 28px; top: 20px; display: flex; align-items: center; gap: 12px;
  }
  .brand__mark { width: 26px; height: 26px; background: var(--brand-blue); }
  .brand__name { font-size: 68px; font-weight: 400; color: var(--brand-blue); line-height: 1; }
</style>
</head>
<body>
  <header class="top-band">
    <div class="top-band__skyline" role="img" aria-label="Photo of glass office towers"></div>
  </header>

  <div class="heading-fade"></div>
  <h1 class="slide-title"><span class="slide-title__accent">Business</span> Progress</h1>
  <p class="slide-intro">Some introduction content here Some introduction content hereSome introduction content hereSome introduction content here Some introduction content hereSome introduction content here</p>

  <svg class="progress-chart" width="1200" height="320" viewBox="0 380 1200 320" aria-label="Bar chart">
    <!-- platform -->
    <polygon points="115,647 1022,647 1022,668 100,668" fill="#d4d4d4"/>
    <rect x="100" y="668" width="922" height="10" fill="#a3a3a3"/>

    <!-- bar 1 -->
    <polygon points="123,442 137,428 221,428 207,442" fill="#c8e27a"/>
    <polygon points="207,442 221,428 221,649 207,663" fill="#6d8d00"/>
    <rect x="123" y="442" width="84" height="221" fill="#a6d300"/>
    <text class="bar-label" x="101" y="414">00.00%</text>

    <!-- bar 2 -->
    <polygon points="259,621 273,613 357,613 343,621" fill="#ff6b6b"/>
    <polygon points="343,621 357,613 357,655 343,663" fill="#b30000"/>
    <rect x="259" y="621" width="84" height="42" fill="#f00000"/>
    <text class="bar-label" x="238" y="610">00.00%</text>

    <!-- bar 3 -->
    <polygon points="382,627 396,619 480,619 466,627" fill="#7fc8ff"/>
    <polygon points="466,627 480,619 480,655 466,663" fill="#006fc0"/>
    <rect x="382" y="627" width="84" height="36" fill="#0a99f2"/>
    <text class="bar-label" x="356" y="613">00.00%</text>

    <!-- bar 4 -->
    <polygon points="505,571 519,557 603,557 589,571" fill="#5f8fd6"/>
    <polygon points="589,571 603,557 603,649 589,663" fill="#002d7a"/>
    <rect x="505" y="571" width="84" height="92" fill="#0047ae"/>
    <text class="bar-label" x="492" y="553">00.00%</text>

    <!-- bar 5 -->
    <polygon points="640,531 654,517 746,517 732,531" fill="#f7ad70"/>
    <polygon points="732,531 746,517 746,649 732,663" fill="#b04c00"/>
    <rect x="640" y="531" width="92" height="132" fill="#ff7200"/>
    <text class="bar-label" x="625" y="509">00.00%</text>

    <!-- bar 6 -->
    <polygon points="780,628 794,622 878,622 864,628" fill="#ffe066"/>
    <polygon points="864,628 878,622 878,657 864,663" fill="#b38900"/>
    <rect x="780" y="628" width="84" height="35" fill="#ffc600"/>
    <text class="bar-label" x="747" y="614">00.00%</text>

    <!-- bar 7 -->
    <polygon points="906,643 920,638 1004,638 990,643" fill="#6fe0a0"/>
    <polygon points="990,643 1004,638 1004,658 990,663" fill="#00703c"/>
    <rect x="906" y="643" width="84" height="20" fill="#00b35a"/>
    <text class="bar-label" x="880" y="640">00.00%</text>
  </svg>

  <footer class="bottom-band">
    <div class="brand">
      <span class="brand__mark"></span>
      <span class="brand__name">TLR</span>
    </div>
  </footer>
</body>
</html>
```